military training website velmotrail.com

I have a website that someone designed I am not happy with. It looks like the designer did not have the artistic ability to make a quality product. the power points are ideas that I had for the website. the business proposal was designed by someone else, and I like the style and font used, the website should reflect this document. The main part of the website should be informational with few pictures, maybe some background images behind or off to the side of the text. I would like to include a generic map with four locations marked, which, when you hover the cursor over them, show a picture of the actual location with an artistic effect or blurred so it doesn't look like a plivora atlas snip, and a picture that resembles what services are offered there, along with the text description, pictures can be found in the documents I attached, also can be stock images. this is outlined in the power points roughly.
Want to have the side menu of the major topics, or at the top, and scroll down a single page to find all of the information we have to offer

Target Market(s)

Special operations military

Industry/Entity Type

military

Coding

Coded - Design and coding required

Number of Pages Required

1 page

Other font styles liked:
• Agency FB

Colors
0054AA
0677BA
7BADD7
CADEEF
E8F1F8
00AB8E
00BBA5
67D7C9
C6EFE9
E9F9F6

Requirements
Must have
• interactive "map"
Nice to have
• professional design features to make it look like a professional website, not a beginner designer

```html
<!DOCTYPE html>
<html lang="en">
<head>
<meta charset="utf-8">
<title>Velmo Trail – SOF Training Range</title>
<link href="https://fonts.googleapis.com/css2?family=IBM+Plex+Sans:wght@500;600;700&family=Roboto:wght@400;500;700&display=swap" rel="stylesheet">
<style>
:root{
  --navy:#111c38;
  --steel:#5585b5;
  --steel-btn:#4a78b0;
  --ice:#e8f4fb;
  --teal:#00ab8e;
  --ink:#1d1d1d;
  --body:#444;
  --white:#fff;
}
*{box-sizing:border-box;margin:0;padding:0}
html,body{width:1200px;height:4539px;overflow:hidden}
body{position:relative;font-family:"Roboto",Arial,sans-serif;color:var(--body);background:var(--white)}
.abs{position:absolute}
h1,h2,h3{font-family:"IBM Plex Sans",Arial,sans-serif;font-weight:700;color:var(--ink)}

/* header */
.topline{left:0;top:0;width:1200px;height:4px;background:var(--steel)}
.header{left:0;top:4px;width:1200px;height:84px;background:var(--white);z-index:3}
.brand{left:103px;top:6px;width:130px;height:130px;border-radius:50%;background:var(--white);border:4px solid var(--navy);display:flex;align-items:center;justify-content:center;text-align:center;z-index:4;font-family:"IBM Plex Sans",sans-serif;font-weight:700;font-size:17px;line-height:1.1;color:var(--navy)}
.nav{font-family:"Roboto",sans-serif;font-weight:500;font-size:13.5px;color:#222}
.nav span{position:absolute;white-space:nowrap}
.socials{display:flex;gap:12px}
.socials i{display:block;width:28px;height:28px;border-radius:50%;background:var(--steel-btn)}

/* hero */
.hero{left:0;top:88px;width:1200px;height:609px;background:linear-gradient(180deg,#3a2a1c 0%,#a9652a 22%,#d9913c 34%,#7a4e2a 55%,#2c241f 78%,#1b1714 100%)}
.hero-sub{left:0;top:320px;width:1200px;text-align:center;font-family:"IBM Plex Sans",sans-serif;font-weight:700;font-size:34px;color:#fff}
.hero-title{left:0;top:365px;width:1200px;text-align:center;font-family:"IBM Plex Sans",sans-serif;font-weight:700;font-size:84px;color:#fff;letter-spacing:1px}
.btn{display:flex;align-items:center;justify-content:center;border-radius:22px;font-family:"Roboto",sans-serif;font-weight:700;color:#fff}
.hero-btn{left:516px;top:498px;width:168px;height:42px;background:var(--steel-btn);font-size:15px}

/* mission */
.mission{left:0;top:697px;width:1200px;height:244px;background:var(--navy)}
.mission h2{position:absolute;left:0;top:60px;width:1200px;text-align:center;color:#fff;font-size:33px}
.mission p{position:absolute;left:180px;top:120px;width:840px;text-align:center;color:#fff;font-size:15.5px;line-height:26px}

/* provide */
.provide-title{left:0;top:1018px;width:1200px;text-align:center;font-size:32px}
.provide-text{left:160px;top:1076px;width:880px;text-align:center;font-size:13px;line-height:25px;color:#333}
.card{top:1203px;width:302px;height:345px;background:#fff;border-radius:14px;box-shadow:0 4px 18px rgba(0,0,0,.09);padding:26px 18px}
.card .ico{width:72px;height:72px;border-radius:50%;background:var(--steel-btn);border:5px solid #cadeef;margin-bottom:18px}
.card h3{font-family:"Roboto",sans-serif;font-weight:500;font-size:17px;margin-bottom:10px}
.card p{font-size:13px;line-height:25px;color:#444;text-align:justify}
.arrow{top:1362px;width:20px;height:26px}

/* qualifications */
.qual{left:0;top:1638px;width:1200px;height:534px;background:var(--ice)}
.qual-photo{left:119px;top:1695px;width:420px;height:420px;border-radius:50%;border:16px solid #c9c9c9;background:radial-gradient(circle at 50% 40%,#bfcbd2 0%,#8a9aa0 45%,#5e6d5a 100%)}
.qual h2{position:absolute;left:590px;top:112px;font-size:33px}
.qual p{position:absolute;left:590px;top:165px;width:490px;font-size:14.5px;line-height:28px;color:#555}
.qual .btn{position:absolute;left:590px;top:378px;width:125px;height:34px;background:var(--steel-btn);font-size:12.5px}

/* map */
.map{left:111px;top:2258px;width:977px;height:622px;background:linear-gradient(135deg,#1d2f52 0%,#2f4a3a 35%,#3c5b3a 60%,#2a4530 100%)}
.pin{width:26px;height:26px;border-radius:50%;background:var(--teal);border:3px solid #7fe0cf;color:#fff;font-weight:700;font-size:18px;line-height:19px;text-align:center}
.tip{left:246px;top:2640px;width:162px;height:168px;background:#fff;border-radius:8px;padding:18px 16px;font-size:11.5px;line-height:23px;color:#222}

/* contact */
.contact{left:0;top:2973px;width:1200px;height:452px;background:var(--steel)}
.contact h2{position:absolute;left:0;top:52px;width:1200px;text-align:center;color:#fff;font-size:33px}
.field{background:#fff;border:1px solid #d6d6d6;border-radius:4px;font-size:13px;color:#888;padding:15px 20px}
.submit{left:537px;top:3313px;width:126px;height:34px;background:var(--navy);font-size:13px}

/* gallery */
.gallery-title{left:0;top:3500px;width:1200px;text-align:center;font-size:33px}
.shot{width:316px;height:238px}

/* footer */
.footer{left:0;top:4163px;width:1200px;height:376px;background:var(--navy)}
.footer .brandf{position:absolute;left:113px;top:60px;width:154px;height:154px;border-radius:50%;background:var(--white);display:flex;align-items:center;justify-content:center;text-align:center;font-family:"IBM Plex Sans",sans-serif;font-weight:700;font-size:19px;line-height:1.1;color:var(--navy)}
.fcol h4{font-family:"IBM Plex Sans",sans-serif;font-weight:700;font-size:15.5px;color:#fff;margin-bottom:10px}
.fcol .rule{width:66px;height:2px;background:var(--steel);margin-bottom:18px}
.links li{list-style:none;color:#fff;font-size:12px;line-height:30px;padding-left:6px}
.cinfo li{list-style:none;display:flex;gap:14px;color:#fff;font-size:12px;line-height:19px;margin-bottom:16px}
.cinfo svg{flex:0 0 14px;margin-top:2px}
.nl p{color:#fff;font-size:12px;line-height:21px;width:240px;margin-bottom:14px}
.nl .inp{width:252px;height:36px;border-radius:18px;background:#fff;display:flex;justify-content:space-between;overflow:hidden}
.nl .inp span{font-size:11px;color:#888;padding:11px 0 0 16px}
.nl .inp b{width:46px;background:var(--steel-btn)}
.bottom{left:0;top:4500px;width:1200px;font-size:12px;color:#fff}
.chat{left:1126px;top:4404px;width:44px;height:44px;border-radius:50%;background:var(--steel-btn)}
</style>
</head>
<body>
<div class="abs topline"></div>
<header class="abs header">
  <nav class="abs nav" style="left:0;top:32px">
    <span style="left:290px">MISSION</span>
    <span style="left:382px">WHAT WE PROVIDE</span>
    <span style="left:542px">MAP</span>
    <span style="left:606px">QUALIFICATIONS</span>
    <span style="left:752px">CONTACT</span>
    <span style="left:848px">GALLERY</span>
  </nav>
  <div class="abs socials" style="left:942px;top:30px" aria-label="Social links"><i></i><i></i><i></i><i></i></div>
</header>
<div class="abs brand">VELMO<br>TRAIL</div>

<section class="abs hero" role="img" aria-label="Sunset photo of troops walking past tiltrotor aircraft on an airfield"></section>
<div class="abs hero-sub">WELCOME TO</div>
<h1 class="abs hero-title">VELMOTRAIL</h1>
<div class="abs btn hero-btn">GET STARTED</div>

<section class="abs mission">
  <h2>MASTER THE MISSION</h2>
  <p>Pioneering realistic training within a strategic theater across the full spectrum of SOF capabilities, liberating warriors from the shackles of logistical burdens and unleashing their full potential to vanquish adversaries</p>
</section>

<h2 class="abs provide-title">WHAT WE PROVIDE</h2>
<p class="abs provide-text">At Velmo Trail, we draw upon years of invaluable experience gained from training at SOF facilities worldwide. Our journey has culminated in the creation of an all-encompassing training site tailored to meet the exacting needs of SOF operators. We provide a comprehensive range of training modalities meticulously crafted to enhance SOF tactics. Anchored by an unwavering commitment to realism and operational effectiveness, we ensure that your warriors are fully prepared to conquer the most demanding challenges they may face.</p>
<svg class="abs arrow" style="left:58px" viewBox="0 0 20 26"><path d="M14 3 4 13l10 10" fill="none" stroke="#222" stroke-width="2.5"/></svg>
<svg class="abs arrow" style="left:1122px" viewBox="0 0 20 26"><path d="M6 3l10 10L6 23" fill="none" stroke="#222" stroke-width="2.5"/></svg>
<article class="abs card" style="left:113px"><div class="ico"></div><h3>Precision Marksmanship</h3><p>Utilizing Tier 1 level instructors alongside seasoned local tactical shooting experts, our comprehensive programs incorporate practice with both steel and paper targets, conducted across multiple shooting locations for varied training environments.</p></article>
<article class="abs card" style="left:449px"><div class="ico"></div><h3>Immersive Scenarios</h3><p>We have transformed a former Soviet military stronghold into a dynamic training environment, meticulously furnished with explosives, pyrotechnics, and a live Opposition Force for verisimilar assault scenarios. Underground lays an intricate tunnel system</p></article>
<article class="abs card" style="left:784px"><div class="ico"></div><h3>Airfield Dominance</h3><p>With a sprawling 7000ft runway available, we provide an expansive canvas for a myriad of airfield operations, including seizures, static line operations, military free fall, and helicopter insertion and extraction techniques.</p></article>

<section class="abs qual">
  <h2>QUALIFICATIONS</h2>
  <p>The founders of Velmo Trail OÜ bring forth a wealth of experience and expertise to the table. A former USAF Combat Controller, with nearly a decade of service in Europe; and a highly esteemed former Estonian Special Operator who graduated BUDs and Ranger School, with a proven track record of business success in Estonia. Together, we are steadfast in our dedication to delivering world-class training experiences, deeply rooted in operational excellence and strategic foresight.</p>
  <div class="btn">LEARN MORE</div>
</section>
<div class="abs qual-photo" role="img" aria-label="Photo of a parachutist in free fall above a river landscape"></div>

<div class="abs map" role="img" aria-label="Satellite map of Estonia with four training sites outlined"></div>
<div class="abs pin" style="left:488px;top:2383px">+</div>
<div class="abs pin" style="left:796px;top:2448px">+</div>
<div class="abs pin" style="left:810px;top:2636px">+</div>
<div class="abs pin" style="left:201px;top:2714px">+</div>
<div class="abs tip">Site-4<br>Inactive Runway<br>Multiple Shooting Lanes<br>1000m Sniper Range<br>Trench Warfare Training<br>Near The Sea For Otb</div>

<section class="abs contact">
  <h2>CONTACT US</h2>
</section>
<div class="abs field" style="left:155px;top:3097px;width:431px;height:48px">Name</div>
<div class="abs field" style="left:610px;top:3097px;width:431px;height:46px">Name</div>
<div class="abs field" style="left:155px;top:3163px;width:431px;height:48px">Email Address</div>
<div class="abs field" style="left:610px;top:3163px;width:434px;height:117px">Message</div>
<div class="abs field" style="left:155px;top:3229px;width:431px;height:48px">Phone Number</div>
<div class="abs btn submit">SUBMIT NOW</div>

<h2 class="abs gallery-title">OUR GALLERY</h2>
<div class="abs shot" style="left:113px;top:3575px;background:linear-gradient(160deg,#e9ecef,#7c9a5a 60%,#4c6a34)" role="img" aria-label="Helicopter landing on a grassy mountain field"></div>
<div class="abs shot" style="left:442px;top:3575px;background:linear-gradient(160deg,#5a6a4a,#3c4a3a 60%,#6a7060)" role="img" aria-label="Two operators reviewing a tablet"></div>
<div class="abs shot" style="left:772px;top:3575px;background:linear-gradient(180deg,#6e8a4a,#4a5a3a 50%,#3a3a3e)" role="img" aria-label="Troops on a runway edge"></div>
<div class="abs shot" style="left:113px;top:3830px;background:linear-gradient(180deg,#4f86c9,#a9c8ea 60%,#dfe9f4)" role="img" aria-label="Tiltrotor aircraft in a blue sky"></div>
<div class="abs shot" style="left:442px;top:3830px;background:linear-gradient(180deg,#4e4238,#8a6a4a 50%,#3a2e26)" role="img" aria-label="Operators with antennas at dusk"></div>
<div class="abs shot" style="left:772px;top:3830px;background:linear-gradient(160deg,#e9ecef,#7c9a5a 60%,#4c6a34)" role="img" aria-label="Helicopter approaching a grassy field"></div>

<footer class="abs footer">
  <div class="brandf">VELMO<br>TRAIL</div>
  <div class="abs fcol" style="left:360px;top:60px">
    <h4>QUICK LINKS</h4><div class="rule"></div>
    <ul class="links"><li>Mission</li><li>What We Provide</li><li>Map</li><li>Qualifications</li><li>Contact</li><li>Gallery</li></ul>
  </div>
  <div class="abs fcol" style="left:555px;top:60px">
    <h4>CONTACT US</h4><div class="rule"></div>
    <ul class="cinfo">
      <li><svg width="14" height="14" viewBox="0 0 24 24"><path fill="#fff" d="M6.6 10.8a15 15 0 0 0 6.6 6.6l2.2-2.2c.3-.3.7-.4 1-.2 1.1.4 2.3.6 3.6.6.6 0 1 .4 1 1V20c0 .6-.4 1-1 1A17 17 0 0 1 3 4c0-.6.4-1 1-1h3.5c.6 0 1 .4 1 1 0 1.2.2 2.4.6 3.6.1.3 0 .7-.2 1z"/></svg>+1 888 888 8888</li>
      <li><svg width="14" height="14" viewBox="0 0 24 24"><path fill="#fff" d="M2 5h20v14H2zm2 2v1l8 5 8-5V7l-8 5z"/></svg>info@velmotrail.com</li>
      <li><svg width="14" height="14" viewBox="0 0 24 24"><path fill="#fff" d="M12 2a7 7 0 0 0-7 7c0 5 7 13 7 13s7-8 7-13a7 7 0 0 0-7-7zm0 9.5A2.5 2.5 0 1 1 12 6a2.5 2.5 0 0 1 0 5.5z"/></svg>123, Lorem ipsum dolor sit amet,<br>adipiscing elit, sed do</li>
      <li><svg width="14" height="14" viewBox="0 0 24 24"><path fill="#fff" d="M6 3h12v5H6zM3 9h18v9h-3v3H6v-3H3zm5 6v4h8v-4z"/></svg>123-456-7890</li>
    </ul>
  </div>
  <div class="abs fcol nl" style="left:830px;top:60px">
    <h4>SUBSCRIBE TO OUR NEWSLETTER</h4><div class="rule"></div>
    <p>Sign up today to get resources on how to attract and retain more customers!</p>
    <div class="inp"><span>Email Address</span><b></b></div>
    <div class="socials" style="margin-top:20px" aria-label="Social links"><i></i><i></i><i></i><i></i></div>
  </div>
</footer>
<div class="abs chat"></div>
<div class="abs bottom">
  <span class="abs" style="left:110px">Copyright© 2024 <u>Velmotrail</u> | All Rights Reserved</span>
  <span class="abs" style="left:808px">Specifications &nbsp;| &nbsp;&nbsp;Site Map &nbsp;| &nbsp;&nbsp;Privacy Policy</span>
</div>
</body>
</html>
```